IT solutions & services company requires stationary makeover

Looking for a consistent modern, professional design across our printed client touch points:
Business Cards
Letterhead
Client proposal
Flyer
Postcard

We provide solutions for SME IT - servers, backups, AV etc, and the ongoing services around them.
we are happy with our logo - please see attached and would like the colour theme to be maintained.

```html
<!DOCTYPE html>
<html lang="en">
<head>
<meta charset="utf-8">
<title>Kestrel – Business Card</title>
<link href="https://fonts.googleapis.com/css2?family=Arimo:ital,wght@0,400;0,700;1,400&display=swap" rel="stylesheet">
<style>
  :root {
    --backdrop: #e9e6e1;
    --card-white: #ffffff;
    --brand-blue: #2b5f93;
    --navy-deep: #1b3550;
    --navy-mid: #24476a;
    --fibre-light: #4f86b8;
    --text-grey: #4a4f55;
    --text-light: #ffffff;
  }
  * { box-sizing: border-box; margin: 0; padding: 0; }
  html, body {
    width: 1200px; height: 801px; overflow: hidden;
    background: var(--backdrop);
    font-family: "Arimo", Arial, sans-serif;
  }
  .stage {
    width: 1200px; height: 801px;
    display: flex; align-items: center; justify-content: center;
  }
  .business-card {
    width: 880px; height: 520px;
    background: var(--card-white);
    display: flex; flex-direction: column;
    box-shadow: 0 6px 24px rgba(0,0,0,0.18);
  }
  .card-header {
    height: 95px;
    display: flex; justify-content: space-between; align-items: center;
    padding: 0 34px 0 36px;
  }
  .brand { display: flex; flex-direction: column; }
  .brand-name {
    font-size: 34px; font-weight: 400; color: var(--text-grey);
    line-height: 1;
  }
  .brand-tagline { font-size: 11px; color: var(--text-grey); margin-top: 5px; }
  .person { text-align: right; }
  .person-name {
    font-size: 36px; font-weight: 400; color: var(--brand-blue);
    line-height: 1.05;
  }
  .person-role { font-size: 17px; font-style: italic; color: var(--text-grey); }
  .card-band {
    height: 355px;
    background: linear-gradient(180deg, var(--navy-mid), var(--navy-deep));
    display: flex; justify-content: space-between;
  }
  .fibre-art {
    width: 470px; height: 100%;
    background: radial-gradient(ellipse at 30% 70%, var(--fibre-light) 0%, var(--navy-mid) 55%, transparent 80%);
  }
  .contact {
    padding: 80px 36px 0 0;
    text-align: right;
    color: var(--text-light);
    font-style: italic; font-size: 22px; line-height: 1.5;
  }
  .card-footer {
    flex: 1;
    display: flex; align-items: center; justify-content: center;
  }
  .website { font-size: 22px; font-weight: 700; color: var(--brand-blue); }
</style>
</head>
<body>
<main class="stage">
  <article class="business-card">
    <header class="card-header">
      <div class="brand">
        <span class="brand-name">Kestrel</span>
        <span class="brand-tagline">tech solutions &amp; services</span>
      </div>
      <div class="person">
        <h1 class="person-name">Rowan Lane</h1>
        <p class="person-role">chief executive officer</p>
      </div>
    </header>
    <section class="card-band">
      <div class="fibre-art" role="img" aria-label="Glowing blue fibre-optic strands fanning out across the dark band"></div>
      <address class="contact">
        03 555 0182<br>
        rlane@kestrel-it.example<br>
        Level 2,<br>
        Harbour Lane,<br>
        Dunedin, NZ
      </address>
    </section>
    <footer class="card-footer">
      <span class="website">www.kestrel-it.example</span>
    </footer>
  </article>
</main>
</body>
</html>
```